Website Refresh

I'm looking to refresh my Squarespace website. www.derekmulvane.com

I am pretty happy with the content but would like a better navigation bar, livelier color choices, consistent type faces, and a more modern look. I am willing to pay extra to implement suggested improvements that would make the site more appealing

```html
<!DOCTYPE html>
<html lang="en">
<head>
<meta charset="utf-8">
<title>Halvard — Derek Mulvane</title>
<link href="https://fonts.googleapis.com/css2?family=Montserrat:wght@400;500;600;700;800&family=Roboto:wght@400;500&family=Fira+Sans:wght@600&display=swap" rel="stylesheet">
<style>
:root{
  --navy:#173a63;
  --purple:#37105c;
  --gold:#e6c66c;
  --gray-bg:#ececee;
  --text:#555;
  --ink:#222;
  --black:#050505;
}
*{box-sizing:border-box;margin:0;padding:0}
html,body{width:1200px;height:3950px;overflow:hidden;background:#fff;font-family:'Roboto',sans-serif;color:var(--ink)}
.page{position:relative;width:1200px;height:3950px}
.abs{position:absolute}
.brand{left:112px;top:22px}
.brand-name{font-family:'Montserrat',sans-serif;font-weight:800;font-size:34px;color:var(--navy);letter-spacing:-1px;line-height:1}
.brand-tag{font-size:9.5px;color:#666;line-height:1.2;margin-top:3px}
.socials{left:626px;top:38px;display:flex;gap:7px}
.dot{width:27px;height:27px;border-radius:50%}
.lang{left:756px;top:42px;font:600 14px 'Montserrat',sans-serif;display:flex;align-items:center;gap:8px}
.lang .flag{width:24px;height:24px;border-radius:50%;background:#c8323a}
.call{left:862px;top:26px;display:flex;align-items:center;gap:12px}
.call-text small{display:block;font:600 14px 'Montserrat',sans-serif;color:#222}
.call-text b{font:700 21px 'Montserrat',sans-serif;color:#222}
.nav{left:0;top:103px;width:1200px;height:58px;background:var(--purple);display:flex;padding-left:131px}
.nav a{color:#fff;font:700 12.5px 'Montserrat',sans-serif;text-decoration:none;padding:0 12px;line-height:58px}
.nav a.active{background:var(--gold);color:var(--purple)}
.hero{left:0;top:161px;width:1200px;height:628px;background:linear-gradient(180deg,#5b544e,#3f3a36 60%,#2e2a28)}
.hero h1{position:absolute;top:258px;width:100%;text-align:center;font:700 41px 'Montserrat',sans-serif;color:#fff}
.hero p{position:absolute;top:326px;left:300px;width:600px;text-align:center;color:#fff;font:600 14.5px/26px 'Montserrat',sans-serif}
.btn{display:inline-block;background:var(--gold);color:var(--purple);font:700 13px 'Montserrat',sans-serif;border-radius:22px;text-align:center}
.hero .btn{position:absolute;left:533px;top:400px;width:134px;height:42px;line-height:42px}
.arrow{width:44px;height:44px;border-radius:50%;background:rgba(255,255,255,.75);top:262px;display:flex;align-items:center;justify-content:center}
.sec-title{width:1200px;left:0;text-align:center;font:700 35px/43px 'Montserrat',sans-serif;color:var(--navy);letter-spacing:-.5px}
.traits{left:112px;top:1023px;width:976px;display:flex;justify-content:space-between}
.trait{width:196px;text-align:center}
.ring{width:192px;height:192px;border-radius:50%;border:3px solid #9a9a9a;margin:0 auto;display:flex;align-items:center;justify-content:center}
.ring.on{border-color:var(--purple)}
.ring-inner{width:170px;height:170px;border-radius:50%;border:4px solid var(--gold);display:flex;align-items:center;justify-content:center}
.trait h3{font:600 20px/26px 'Fira Sans',sans-serif;color:#222;margin-top:34px}
.lead{left:0;width:1200px;text-align:center;font:600 22px/26px 'Montserrat',sans-serif;color:var(--navy);letter-spacing:-.3px}
.photo{border-radius:4px}
.about-text{left:599px;top:1532px;width:490px;font:400 13.5px/21.5px 'Montserrat',sans-serif;color:#555}
.about-text p+p{margin-top:21px}
.video-sec{left:0;top:1915px;width:1200px;height:794px;background:var(--gray-bg)}
.sub{left:0;width:1200px;text-align:center;font:400 17.5px/28px 'Roboto',sans-serif;color:#444}
.vid{background:linear-gradient(160deg,#4d6a58,#6b7f86 45%,#8a8f98);border-radius:3px}
.play{position:absolute;left:50%;top:50%;transform:translate(-50%,-50%)}
.blog-band{left:0;top:2709px;width:1200px;height:220px;background:var(--purple)}
.kicker{left:0;top:2750px;width:1200px;text-align:center;font:400 22px 'Montserrat',sans-serif;color:#fff}
.blog-title{left:0;top:2786px;width:1200px;text-align:center;font:800 37px 'Montserrat',sans-serif;color:#fff}
.card{top:2865px;width:314px;height:398px;background:#fff;box-shadow:0 4px 14px rgba(0,0,0,.12)}
.card .img{height:272px;border-bottom:4px solid var(--purple);position:relative}
.date{position:absolute;left:50%;bottom:-4px;transform:translateX(-50%);background:var(--gold);font:700 11.5px 'Montserrat',sans-serif;padding:5px 14px;color:#222}
.card h4{font:700 14.5px/24px 'Montserrat',sans-serif;text-align:center;margin-top:20px;padding:0 6px;color:#222;white-space:nowrap}
.card .more{display:block;text-align:center;font:500 12px 'Montserrat',sans-serif;text-decoration:underline;color:#333;margin-top:6px}
.read{left:498px;top:3298px;width:204px;height:36px;line-height:36px}
.footer{left:0;top:3445px;width:1200px;height:505px;background:var(--black);color:#fff}
.f-h{font:500 18px 'Roboto',sans-serif}
.field{position:absolute;background:#fff;border:1px solid #ccc;font:400 13px 'Roboto',sans-serif;color:#666;padding:12px 18px}
.submit{left:112px;top:349px;width:134px;height:46px;line-height:46px;font-size:15px;color:#222;border-radius:24px}
.links li{list-style:none;font:400 15px 'Roboto',sans-serif;margin-bottom:12px;padding-left:22px;position:relative}
.links li::before{content:"»";position:absolute;left:0}
.contact div{font:400 15px/24px 'Roboto',sans-serif;display:flex;gap:14px}
.rule{left:112px;top:443px;width:976px;height:1px;background:#444}
.copy{left:0;top:462px;width:1200px;text-align:center;font:400 15px 'Roboto',sans-serif}
</style>
</head>
<body>
<div class="page">

  <div class="abs brand">
    <div class="brand-name">HALVARD</div>
    <div class="brand-tag">Private advisory boards for CEOs,<br>executives and business owners.</div>
  </div>
  <div class="abs socials">
    <div class="dot" style="background:#3b5aa0"></div>
    <div class="dot" style="background:#2aa3e8"></div>
    <div class="dot" style="background:#e0332d"></div>
  </div>
  <div class="abs lang">Eng <svg width="9" height="6" viewBox="0 0 9 6"><path d="M1 1l3.5 3.5L8 1" fill="none" stroke="#222" stroke-width="1.4"/></svg><span class="flag"></span></div>
  <div class="abs call">
    <svg width="48" height="48" viewBox="0 0 48 48"><circle cx="24" cy="24" r="21.5" fill="none" stroke="var(--purple)" stroke-width="3"/><path d="M16 14c2-1 3 0 4 3l1 3c0 2-2 2-2 3 1 3 4 6 7 7 1 0 1-2 3-2l3 1c3 1 4 2 3 4-1 3-4 4-7 3-6-2-12-8-14-14-1-3 0-7 2-8z" fill="var(--purple)"/></svg>
    <div class="call-text"><small>Call us Today :</small><b>+1 888 888 8888</b></div>
  </div>

  <nav class="abs nav">
    <a class="active">ABOUT</a><a>MEMBER VIDEO TESTIMONIALS</a><a>TESTIMONIALS</a><a>SUCCESS STORIES</a><a>DEREK'S BLOG</a><a>DEREK MULVANE BIO</a><a>JOIN THE GROUP</a>
  </nav>

  <section class="abs hero" role="img" aria-label="Photo of executives in a meeting room discussion">
    <div class="abs arrow" style="left:69px"><svg width="10" height="14"><path d="M8 2L3 7l5 5" fill="none" stroke="#444" stroke-width="1.6"/></svg></div>
    <div class="abs arrow" style="left:1086px"><svg width="10" height="14"><path d="M2 2l5 5-5 5" fill="none" stroke="#444" stroke-width="1.6"/></svg></div>
    <h1>TURNING GOOD CEOS INTO GREAT CEOS</h1>
    <p>Our award winning CEOs will help you make better decisions for your company, family, and community .</p>
    <span class="btn">GET STARTED</span>
  </section>

  <h2 class="abs sec-title" style="top:897px">MEMBERSHIP IS BY INVITATION<br>ONLY FOR THOSE WHO</h2>

  <div class="abs traits">
    <div class="trait"><div class="ring"><div class="ring-inner">
      <svg width="58" height="58" viewBox="0 0 58 58"><rect x="3" y="26" width="11" height="28" rx="2" fill="var(--purple)"/><path d="M18 26l10-18c3-4 8-2 7 3l-3 11h16c4 0 6 4 4 7 2 2 1 5-1 6 1 2 0 5-2 6 1 3-1 6-4 6H22c-2 0-4-2-4-4z" fill="var(--purple)"/></svg>
    </div></div><h3>Open to being<br>challenged</h3></div>
    <div class="trait"><div class="ring"><div class="ring-inner">
      <svg width="58" height="50" viewBox="0 0 58 50"><path d="M5 4v40h49" fill="none" stroke="var(--purple)" stroke-width="5"/><path d="M12 34l12-12 8 8 14-14" fill="none" stroke="var(--purple)" stroke-width="5"/><path d="M40 12h10v10z" fill="var(--purple)"/></svg>
    </div></div><h3>Commit to double<br>digit growth</h3></div>
    <div class="trait"><div class="ring on"><div class="ring-inner">
      <svg width="62" height="54" viewBox="0 0 62 54"><rect x="3" y="3" width="56" height="36" rx="3" fill="none" stroke="var(--purple)" stroke-width="6"/><rect x="25" y="39" width="12" height="8" fill="var(--purple)"/><rect x="15" y="46" width="32" height="6" rx="2" fill="var(--purple)"/></svg>
    </div></div><h3>Ongoing<br>learning</h3></div>
    <div class="trait"><div class="ring"><div class="ring-inner">
      <svg width="60" height="58" viewBox="0 0 60 58"><path d="M30 2l8.5 18 19.5 2.5-14.5 13.5 4 19.5L30 45.5 12.5 55.5l4-19.5L2 22.5 21.5 20z" fill="var(--purple)"/></svg>
    </div></div><h3>Giving &amp; receiving<br>honest feedback</h3></div>
  </div>

  <p class="abs lead" style="top:1375px">If you are lonely with no one you can trust to talk through tough decisions<br>If you don’t have the right people in the right seats</p>
  <p class="abs lead" style="top:1452px">If you seek financial independence, professional and personal growth, and<br>avoiding burnout; our group might be right for you.</p>

  <div class="abs photo" style="left:112px;top:1538px;width:461px;height:282px;background:linear-gradient(135deg,#5e6a66,#8b8f8a 55%,#3a3e3f)" role="img" aria-label="Photo of a peer group meeting around a conference table"></div>
  <div class="abs about-text">
    <p>After many years in the business world as the founder/CEO of six for-profit and five not-for-profit corporations, I understand the huge responsibility you have for making the right decisions for your company, the personal well-being of your employees and yourself.</p>
    <p>Our Halvard group is made up of 15 other smart CEOs who have been where you are. We meet monthly in a safe, confidential environment to discuss critical business decisions, opportunities, and challenges. Additionally I meet with each member two hours/monthly for a private coaching session.</p>
  </div>
  <span class="abs btn" style="left:599px;top:1780px;width:137px;height:41px;line-height:41px">LEARN MORE</span>

  <section class="abs video-sec"></section>
  <h2 class="abs sec-title" style="top:2004px">OUR VIDEO</h2>
  <p class="abs sub" style="top:2057px">Our award winning CEOs will help you make better decisions for your<br>company, family, and community</p>
  <div class="abs vid" style="left:113px;top:2160px;width:438px;height:450px" role="img" aria-label="Video thumbnail of a member testimonial">
    <svg class="play" width="52" height="52" viewBox="0 0 52 52"><circle cx="26" cy="26" r="24" fill="rgba(255,255,255,.85)"/><path d="M21 16l15 10-15 10z" fill="var(--purple)"/></svg>
  </div>
  <div class="abs vid" style="left:562px;top:2160px;width:259px;height:221px" role="img" aria-label="Video thumbnail of a member testimonial"><svg class="play" width="10" height="10"><path d="M2 1l7 4-7 4z" fill="#fff"/></svg></div>
  <div class="abs vid" style="left:829px;top:2160px;width:260px;height:221px" role="img" aria-label="Video thumbnail of a member testimonial"><svg class="play" width="10" height="10"><path d="M2 1l7 4-7 4z" fill="#fff"/></svg></div>
  <div class="abs vid" style="left:562px;top:2390px;width:259px;height:220px" role="img" aria-label="Video thumbnail of a member testimonial"><svg class="play" width="10" height="10"><path d="M2 1l7 4-7 4z" fill="#fff"/></svg></div>
  <div class="abs vid" style="left:829px;top:2390px;width:260px;height:220px" role="img" aria-label="Video thumbnail of a member testimonial"><svg class="play" width="10" height="10"><path d="M2 1l7 4-7 4z" fill="#fff"/></svg></div>

  <section class="abs blog-band"></section>
  <div class="abs kicker">DEREK’S BLOG</div>
  <h2 class="abs blog-title">LATEDT NEWS AND UPDATES</h2>

  <article class="abs card" style="left:112px">
    <div class="img" style="background:linear-gradient(150deg,#7c7a74,#b3aaa0 50%,#4b4c50)" role="img" aria-label="Photo of a team meeting"><span class="date">Jan 07, 2022</span></div>
    <h4>WHAT ARE OKRS AND HOW<br>YOUR TEAM SHOULD ADOPT THEM</h4><span class="more">Learn More &gt;</span>
  </article>
  <article class="abs card" style="left:443px">
    <div class="img" style="background:linear-gradient(180deg,#4f8a86,#6a6e78 50%,#3d3f4a)" role="img" aria-label="Group photo of peer CEOs"><span class="date">Jan 07, 2022</span></div>
    <h4>IMPRESSIVE PEER CEOS<br>JOIN A DIVERSE BLEND OF 17</h4><span class="more">Learn More &gt;</span>
  </article>
  <article class="abs card" style="left:775px">
    <div class="img" style="background:linear-gradient(180deg,#fbe47a,#f5a623 55%,#e8441e)" role="img" aria-label="Growth graphic showing a 4.6 percent increase for member companies"><span class="date">Jan 07, 2022</span></div>
    <h4>PROVEN HALVARD METHODOLOGY<br>ACCORDING TO CARROW &amp; LINDELL,</h4><span class="more">Learn More &gt;</span>
  </article>
  <span class="abs btn read">READ MORE NEWS</span>

  <footer class="abs footer">
    <div class="abs f-h" style="left:112px;top:112px">GET IN TOUCH</div>
    <div class="field" style="left:112px;top:158px;width:234px;height:38px">First Name</div>
    <div class="field" style="left:354px;top:158px;width:234px;height:38px">Last Name</div>
    <div class="field" style="left:112px;top:207px;width:234px;height:38px">Email</div>
    <div class="field" style="left:354px;top:207px;width:234px;height:38px">phone number</div>
    <div class="field" style="left:112px;top:256px;width:476px;height:72px">Message</div>
    <span class="abs btn submit">SUBMIT</span>

    <div class="abs f-h" style="left:650px;top:112px">QUICK LINKS</div>
    <ul class="abs links" style="left:650px;top:151px">
      <li>Home</li><li>About Us</li><li>Meet Our Staff</li><li>Our Services</li><li>Testimonials</li><li>Contact Us</li>
    </ul>

    <div class="abs f-h" style="left:847px;top:112px">CONTACT US</div>
    <div class="abs contact" style="left:850px;top:155px">
      <div><svg width="12" height="16" viewBox="0 0 12 16" style="margin-top:4px"><path d="M6 0a6 6 0 016 6c0 4-6 10-6 10S0 10 0 6a6 6 0 016-6z" fill="#fff"/><circle cx="6" cy="6" r="2.2" fill="#000"/></svg><span>Lorem ipsum dolor sit amet,<br>consectetur adipi</span></div>
      <div style="margin-top:30px"><svg width="12" height="16" viewBox="0 0 12 16" style="margin-top:4px"><rect x="1.5" y="1" width="9" height="14" rx="1.5" fill="none" stroke="#fff" stroke-width="1.5"/></svg><span>+1 888 888 8888</span></div>
      <div style="margin-top:14px"><svg width="16" height="12" viewBox="0 0 16 12" style="margin-top:6px"><rect x="1" y="1" width="14" height="10" fill="none" stroke="#fff" stroke-width="1.4"/><path d="M1 1l7 6 7-6" fill="none" stroke="#fff" stroke-width="1.4"/></svg><span>info@companyname.com</span></div>
    </div>

    <div class="abs f-h" style="left:650px;top:369px">STAY CONNECTED :</div>
    <div class="abs dot" style="left:850px;top:365px;width:31px;height:31px;background:#3b5aa0"></div>
    <div class="abs dot" style="left:889px;top:365px;width:31px;height:31px;background:#c21c8f"></div>

    <div class="abs rule"></div>
    <div class="abs copy">© 2022 Company Name &nbsp;| All Rights Reserved | Terms and Conditions</div>
  </footer>

</div>
</body>
</html>
```